Wholesale Catalogue Design for Greeting Cards

Fern Ink is a small letterpress printery, I would like to have a wholesale catalogue designed for my range of letterpress greeting cards. I currently have 30 cards in my collection, I can supply photos, I want to be able to add to the catalogue in the future. I also want the design to represent my card designs: fun, colourful and with an elegant edge, featuring a mix of my original illustrations and hand lettering along with downloadable designs and fonts.
I would like to be able to email the catalogue to my wholesale customers and to be able to print the catalogue to use with new/potential wholesale customers.

Target Market(s)

Small boutique retailers, gift shops, baby/kids gift shops, florists

Industry/Entity Type

Wholesale

Font styles to use
Serif

Colors
eea4c8

Requirements
Must have
• I have been using baskerville font in my branding, so it would be good to include this in the design. I can provide photos and text. I also have a pink and black logo (seen attached), it would be great if the design can incorporate some of the same colour scheme.
Nice to have
• I have added some pics below of other catalogues I like the layout of.
• You can also view my work at craftly.com/fernink or ferninkdesign.com
• * I believe I have now loaded all the relevant photos and info
• ** I have uploaded some pics of my attempt at a wholesale catalogue and my current order sheet as this outlines the products I want in the catalogue and the different card sections. my catalogue attempt has more recent photos. I will upload photos of the remaining products by end of today (27.2.16)

```html
<!DOCTYPE html>
<html lang="en">
<head>
<meta charset="utf-8">
<title>Fern Ink Wholesale Catalogue</title>
<link rel="stylesheet" href="https://fonts.googleapis.com/css2?family=Libre+Baskerville:ital,wght@0,400;0,700;1,400&display=swap">
<style>
  :root {
    --pink: #f1a9ae;
    --pink-soft: #eea4c8;
    --frame: #f2c4c8;
    --ink: #111111;
    --alert: #e0323a;
    --paper: #ffffff;
    --logo-bg: #f7f7f7;
  }
  * { margin: 0; padding: 0; box-sizing: border-box; }
  html, body {
    width: 1200px; height: 424px; overflow: hidden;
    background: var(--paper);
    font-family: "Libre Baskerville", Baskerville, Georgia, serif;
    color: var(--ink);
  }
  .spread { position: relative; width: 1200px; height: 424px; }
  .page { position: absolute; top: 0; width: 600px; height: 424px; }
  .page--general { left: 0; }
  .page--mothers { left: 600px; }

  .section-title {
    position: absolute; left: 35px; top: 35px;
    font-size: 16px; font-weight: 400; letter-spacing: 0.5px;
    color: var(--pink); text-transform: uppercase;
  }
  .brand {
    position: absolute; left: 405px; top: 26px; width: 159px; height: 42px;
    background: var(--logo-bg);
    display: flex; align-items: center; justify-content: center; gap: 6px;
  }
  .brand__dot { width: 7px; height: 7px; border-radius: 50%; background: var(--pink); }
  .brand__name { font-size: 20px; color: var(--pink); }

  .terms {
    position: absolute; left: 35px; top: 70px; width: 530px;
    font-size: 6.2px; line-height: 1.45;
  }
  .terms__label { color: var(--pink); text-transform: uppercase; }

  .product { position: absolute; width: 260px; height: 126px; }
  .product__photo {
    position: absolute; left: 0; top: 0; width: 119px; height: 126px;
    border: 1px solid var(--frame);
  }
  .product__info { position: absolute; left: 127px; top: 2px; width: 135px; height: 124px; }
  .product__name { font-size: 8.6px; font-weight: 700; line-height: 1.2; }
  .product__sku, .product__specs li { font-size: 6.4px; line-height: 1.5; }
  .product__specs { list-style: none; }
  .product__specs li::before { content: "\2022\00a0"; }
  .stars { color: var(--alert); }
  .product__price { position: absolute; left: 0; bottom: 0; font-size: 6.4px; line-height: 1.45; }
  .product__price sup { font-size: 4.5px; }

  .order-line {
    position: absolute; left: 45px; top: 388px;
    font-size: 10.2px; color: var(--pink); letter-spacing: 0.2px; text-transform: uppercase;
  }

  .photo--caravan { background: linear-gradient(160deg, #f4ec9a 0%, #fbf6cf 35%, #ffffff 55%, #f3f1ea 100%); }
  .photo--congrats { background: radial-gradient(circle at 38% 30%, #ead0d6 0%, #f6eef0 40%, #f1ece9 100%); }
  .photo--sympathy { background: linear-gradient(150deg, #f3f1ec 0%, #ffffff 50%, #e8e4dc 100%); }
  .photo--marvellous { background: linear-gradient(120deg, #c8bfc6 0%, #ffffff 30%, #f4e6f1 60%, #cfc4cb 100%); }
  .photo--supermum { background: linear-gradient(140deg, #e05aa6 0%, #f3f0ee 25%, #ffffff 55%, #f4d2d8 100%); }
  .photo--flower { background: linear-gradient(150deg, #ede9df 0%, #fbf9f6 45%, #f4ecea 100%); }
</style>
</head>
<body>
<div class="spread">

  <section class="page page--general">
    <h2 class="section-title">General</h2>
    <div class="brand"><span class="brand__dot"></span><span class="brand__name">Fern Ink</span></div>
    <p class="terms"><span class="terms__label">Wholesale terms</span> Opening order minimum $80. Reorder minimum $50. Payment due at time of order. Payments can be made by EFT (electronic funds transfer) or PayLink. Orders will ship within 10 business days of order date. Orders shipped by Coastal Post. All cards are packaged in a clear cello wrapper and the Fern Ink name printed on the back of each card.</p>

    <article class="product" style="left:35px; top:110px;">
      <div class="product__photo photo--caravan" role="img" aria-label="Letterpress card with a yellow vintage caravan illustration on a yellow envelope"></div>
      <div class="product__info">
        <h3 class="product__name">Village Caravan</h3>
        <p class="product__sku">Sku# F001</p>
        <ul class="product__specs">
          <li>Letterpress printed in <span class="stars">*******</span></li>
          <li>Printed on 300 gsm white cotton card</li>
          <li>Size 10x14 cm when folded</li>
          <li>Accompanied by a 100% recycled leafline C6 envelope</li>
        </ul>
        <p class="product__price">Retail $6<sup>50</sup><br>Wholesale $3<sup>55</sup></p>
      </div>
    </article>

    <article class="product" style="left:303px; top:110px;">
      <div class="product__photo photo--congrats" role="img" aria-label="Letterpress congratulations card with pink sunburst and gold lettering"></div>
      <div class="product__info">
        <h3 class="product__name">Congratulations</h3>
        <p class="product__sku">Sku# F002</p>
        <ul class="product__specs">
          <li>Letterpress printed in <span class="stars">*******</span></li>
          <li>Printed on 300 gsm white cotton card</li>
          <li>Size 10x14 cm when folded</li>
          <li>Accompanied by a 100% recycled leafline C6 envelope</li>
        </ul>
        <p class="product__price">Retail $6<sup>50</sup><br>Wholesale $3<sup>55</sup></p>
      </div>
    </article>

    <article class="product" style="left:35px; top:248px;">
      <div class="product__photo photo--sympathy" role="img" aria-label="White sympathy card with a small dove and brown script lettering beside baby's breath"></div>
      <div class="product__info">
        <h3 class="product__name">Sympathy</h3>
        <p class="product__sku">Sku# F003</p>
        <ul class="product__specs">
          <li>Letterpress printed in <span class="stars">*******</span></li>
          <li>Printed on 300 gsm white cotton card</li>
          <li>Size 10x14 cm when folded</li>
          <li>Accompanied by a 100% recycled leafline C6 envelope</li>
        </ul>
        <p class="product__price">Retail $6<sup>50</sup><br>Wholesale $3<sup>55</sup></p>
      </div>
    </article>

    <p class="order-line">To place an order call or email Maya +61(0) 400 555 218 maya@ferninkdesign.com</p>
  </section>

  <section class="page page--mothers">
    <h2 class="section-title">Mother’s Day</h2>
    <div class="brand"><span class="brand__dot"></span><span class="brand__name">Fern Ink</span></div>
    <p class="terms"><span class="terms__label">Wholesale terms</span> Opening order minimum $80. Reorder minimum $50. Payment due at time of order. Payments can be made by EFT (electronic funds transfer) or PayLink. Orders will ship within 10 business days of order date. Orders shipped by Coastal Post. All cards are packaged in a clear cello wrapper and the Fern Ink name printed on the back of each card.</p>

    <article class="product" style="left:35px; top:110px;">
      <div class="product__photo photo--marvellous" role="img" aria-label="White card with magenta Marvellous Mum script lettering among dried flowers"></div>
      <div class="product__info">
        <h3 class="product__name">Marvellous Mum</h3>
        <p class="product__sku">Sku# G001</p>
        <ul class="product__specs">
          <li>Letterpress printed in <span class="stars">*******</span></li>
          <li>Printed on 300 gsm white cotton card</li>
          <li>Size 10x14 cm when folded</li>
          <li>Accompanied by a 100% recycled leafline C6 envelope</li>
        </ul>
        <p class="product__price">Retail $6<sup>50</sup><br>Wholesale $3<sup>55</sup></p>
      </div>
    </article>

    <article class="product" style="left:303px; top:110px;">
      <div class="product__photo photo--supermum" role="img" aria-label="Colourful Super Duper Mum lettered card in pink and yellow beside a pink flower"></div>
      <div class="product__info">
        <h3 class="product__name">Super Mum</h3>
        <p class="product__sku">Sku# G002</p>
        <ul class="product__specs">
          <li>Letterpress printed in <span class="stars">*******</span></li>
          <li>Printed on 300 gsm white cotton card</li>
          <li>Size 10x14 cm when folded</li>
          <li>Accompanied by a 100% recycled leafline C6 envelope</li>
        </ul>
        <p class="product__price">Retail $6<sup>50</sup><br>Wholesale $3<sup>55</sup></p>
      </div>
    </article>

    <article class="product" style="left:35px; top:248px;">
      <div class="product__photo photo--flower" role="img" aria-label="Pale card with soft pink Happy Mother's Day lettering and a green flower stem"></div>
      <div class="product__info">
        <h3 class="product__name">Happy Mother’s Day - flower</h3>
        <p class="product__sku">Sku# G003</p>
        <ul class="product__specs">
          <li>Letterpress printed in <span class="stars">*******</span></li>
          <li>Printed on 300 gsm white cotton card</li>
          <li>Size 10x14 cm when folded</li>
          <li>Accompanied by a 100% recycled leafline C6 envelope</li>
        </ul>
        <p class="product__price">Retail $6<sup>50</sup><br>Wholesale $3<sup>55</sup></p>
      </div>
    </article>

    <p class="order-line">To place an order call or email Maya +61(0) 400 555 218 maya@ferninkdesign.com</p>
  </section>

</div>
</body>
</html>
```